Business Card Design Project

We need a business card for a new technology services company. We develop software and implement software packages for our business customers and although we will begin with just one or two service offerings, our service offerings will expand over time. Our name comes from the an author, KL Barrow, and his "idea" was that opportunity should be based on ability and achievement, not on social status.

We would like to see a design that is standard in its size and shape, but stands apart in its dramatic color contrasts. The card should not use too many colors - the colors used in the background should highlight the brilliant blues of the logo (see attachment) to dramatic effect. The background should not be white.

If necessary, you can change the color of the words "KL Barrow", but not the word "Idea".

Card size should be U.S. standard 2 inches by 3.5 inches and provide for 1/8 inch bleed area on each side.

We need a design for both sides of the business card, one side communicating the company logo and contact information, the other side being purely graphical, incorporating the logo but no other information.

Contact Information Required:
Kate Brook
KateBrook@klbarrowvista.com
614-387-2259

Target Market(s)

Business executives

Industry/Entity Type

Software

Requirements
Must have
• It must have the full company logo on one side, and at least the graphic element of the logo on the other. Either that or the full logo on both.
Nice to have
• It would be nice to have a design that could work without needing two different textures. For example, it would be nice if the entire card could be shiny, not just parts of the card.

It would also be nice if texture is something we could add later.
Should not have
• The card should not use the color green.

```html
<!DOCTYPE html>
<html lang="en">
<head>
<meta charset="utf-8">
<title>KL Barrow Vista – Business Card</title>
<link rel="stylesheet" href="https://fonts.googleapis.com/css2?family=Raleway:wght@400;700&family=Open+Sans:wght@400;700&display=swap">
<style>
  :root {
    --page: #e7e7e9;
    --card-dark: #1b1c1e;
    --card-mid: #34363a;
    --brand-blue: #1d9be0;
    --brand-blue-deep: #0f7fc2;
    --swoosh-grey: #b9bcc0;
    --logo-grey: #cfd2d6;
    --text-white: #ffffff;
  }
  * { box-sizing: border-box; margin: 0; padding: 0; }
  html, body { width: 1200px; height: 720px; overflow: hidden; }
  body {
    background: var(--page);
    position: relative;
    font-family: "Open Sans", Arial, sans-serif;
  }
  .card {
    position: absolute;
    top: 205px;
    width: 540px;
    height: 309px;
    overflow: hidden;
    box-shadow: 0 8px 24px rgba(0,0,0,.22);
  }
  .card--front { left: 40px; }
  .card--back { left: 620px; }
  .card__texture {
    position: absolute; inset: 0;
    background: radial-gradient(ellipse at 55% 40%, var(--card-mid) 0%, var(--card-dark) 75%);
  }
  .card__wave { position: absolute; inset: 0; width: 100%; height: 100%; }
  .wordmark {
    position: absolute;
    font-family: "Raleway", Arial, sans-serif;
    font-weight: 400;
    color: var(--logo-grey);
    letter-spacing: -1px;
    white-space: nowrap;
  }
  .card--front .wordmark { left: 28px; top: 104px; font-size: 40px; }
  .card--back .wordmark {
    left: 0; right: 0; top: 118px;
    text-align: center; font-size: 54px;
  }
  .brand-dot {
    position: absolute;
    width: 42px; height: 42px;
    border-radius: 50%;
    background: var(--brand-blue);
  }
  .card--front .brand-dot { left: 330px; top: 30px; }
  .card--back .brand-dot { left: 249px; top: 52px; opacity: .45; }
  .holder-name {
    position: absolute;
    left: 34px; top: 176px;
    font-weight: 700;
    font-size: 18px;
    letter-spacing: .5px;
    color: var(--brand-blue);
  }
  .contact {
    position: absolute;
    right: 22px;
    list-style: none;
    color: var(--text-white);
    font-size: 14px;
    text-align: right;
  }
  .contact--phone { top: 132px; }
  .contact--email { top: 170px; }
  .contact li { display: flex; align-items: center; justify-content: flex-end; gap: 7px; }
  .contact svg { width: 13px; height: 13px; fill: var(--text-white); }
</style>
</head>
<body>

<section class="card card--front" aria-label="Card front">
  <div class="card__texture" role="img" aria-label="Dark charcoal wood grain texture"></div>
  <svg class="card__wave" viewBox="0 0 540 309" preserveAspectRatio="none" aria-hidden="true">
    <path d="M0,309 L0,278 C140,292 280,250 380,170 C430,130 480,108 540,100 L540,309 Z" fill="var(--brand-blue)"/>
    <path d="M0,278 C140,292 280,250 380,170 C430,130 480,108 540,100 L540,92 C470,100 420,124 370,164 C270,244 140,284 0,270 Z" fill="var(--card-dark)"/>
    <path d="M0,262 C160,276 290,230 380,150 C430,108 480,90 540,84" fill="none" stroke="var(--swoosh-grey)" stroke-width="7"/>
    <path d="M0,300 C140,309 260,290 340,250" fill="none" stroke="var(--swoosh-grey)" stroke-width="6"/>
  </svg>
  <span class="brand-dot" aria-hidden="true"></span>
  <p class="wordmark">KLBarrowVista</p>
  <p class="holder-name">KATE BROOK</p>
  <ul class="contact contact--phone">
    <li><svg viewBox="0 0 24 24" aria-hidden="true"><path d="M6.6 10.8a15.1 15.1 0 0 0 6.6 6.6l2.2-2.2a1 1 0 0 1 1-.25 11.4 11.4 0 0 0 3.6.57 1 1 0 0 1 1 1V20a1 1 0 0 1-1 1A17 17 0 0 1 3 4a1 1 0 0 1 1-1h3.5a1 1 0 0 1 1 1c0 1.25.2 2.45.57 3.6a1 1 0 0 1-.25 1z"/></svg>614-387-2259</li>
  </ul>
  <ul class="contact contact--email">
    <li><svg viewBox="0 0 24 24" aria-hidden="true"><path d="M2 5h20v14H2z M4 7v.5l8 5 8-5V7l-8 5z" fill-rule="evenodd"/></svg>KateBrook@klbarrowvista.com</li>
  </ul>
</section>

<section class="card card--back" aria-label="Card back">
  <div class="card__texture" role="img" aria-label="Dark charcoal wood grain texture"></div>
  <span class="brand-dot" aria-hidden="true"></span>
  <p class="wordmark">KLBarrowVista</p>
</section>

</body>
</html>
```